BrindleStaffing Business Card Design

We are a staffing company finding positions for dedicated nurses and physicians.

Target Market(s)

Business Professionals

Industry/Entity Type

Staffing

Contact Information for Business Card

Gordon Pratley
Chairman
417 39th Avenue South
SAINT PETERSBURG FL 33712
813-555-4172 Mobile
813-555-8036 Fax
gpratley@brindlestaffing.com
www.brindlestaffing.com

Font styles to use
Sans Serif

Colors
fbee3e
f04a50
f37122

Requirements
Must have
• Logo Attached, see colors below. We'd like to see Yellow, Orange and Red.

```html
<!DOCTYPE html>
<html lang="en">
<head>
<meta charset="utf-8">
<title>BrindleStaffing Business Card</title>
<link rel="stylesheet" href="https://fonts.googleapis.com/css2?family=Source+Sans+3:wght@400;700&display=swap">
<style>
  :root {
    --sun: #fbee3e;
    --ember: #f37122;
    --coral: #f04a50;
    --black: #000000;
    --white: #ffffff;
    --stage-light: #9a9a9c;
    --stage-dark: #434243;
  }
  * { margin: 0; padding: 0; box-sizing: border-box; }
  html, body { width: 1200px; height: 1135px; overflow: hidden; }
  body {
    position: relative;
    font-family: "Source Sans 3", sans-serif;
    background: radial-gradient(ellipse 720px 640px at 585px 545px, var(--stage-light) 0%, #6e6e70 55%, var(--stage-dark) 100%);
  }
  .card {
    position: absolute;
    width: 716px;
    height: 409px;
    overflow: hidden;
  }
  .card-front { left: 386px; top: 103px; border-radius: 16px; background: var(--black); }
  .card-back { left: 103px; top: 583px; border-radius: 35px; background: var(--coral); }
  .front-art { position: absolute; inset: 0; width: 100%; height: 100%; }
  .line { position: absolute; line-height: 1; white-space: nowrap; }
  .brand-front {
    left: 25px; top: 104px;
    font-size: 54px; font-weight: 700; letter-spacing: -1px;
    color: var(--coral);
  }
  .holder-name {
    right: 33px; top: 42px;
    font-size: 25px; font-weight: 700; color: var(--sun);
  }
  .holder-title {
    right: 33px; top: 73px;
    font-size: 21px; font-weight: 400; color: var(--ember);
  }
  .contact {
    right: 36px;
    font-size: 18px; color: var(--white);
    display: flex; align-items: center; gap: 7px;
  }
  .contact svg { width: 17px; height: 17px; flex: none; }
  .contact-phone { top: 262px; }
  .contact-fax { top: 296px; }
  .contact-email { top: 330px; }
  .contact-web { top: 364px; }
  .address {
    left: 26px; font-size: 18px; color: var(--white);
  }
  .address-street { top: 337px; }
  .address-city { top: 364px; }
  .brand-back {
    left: 0; right: 0; top: 134px; text-align: center;
    font-size: 74px; font-weight: 700; letter-spacing: -1.5px;
    color: var(--white);
  }
  .web-back {
    left: 0; right: 0; top: 253px; text-align: center;
    font-size: 21px; letter-spacing: 2.6px; color: var(--white);
  }
  .web-back b { font-weight: 700; }
</style>
</head>
<body>

<section class="card card-front" aria-label="Business card front">
  <svg class="front-art" viewBox="0 0 810 462" preserveAspectRatio="none" aria-hidden="true">
    <rect width="810" height="462" fill="var(--black)"/>
    <g>
      <path transform="translate(0,-16)" d="M0,225 C110,330 250,370 450,312 S700,215 810,250 L810,480 L0,480 Z" fill="var(--sun)"/>
      <path transform="translate(0,-13)" d="M0,225 C110,330 250,370 450,312 S700,215 810,250 L810,480 L0,480 Z" fill="var(--coral)"/>
      <path transform="translate(0,-5)" d="M0,225 C110,330 250,370 450,312 S700,215 810,250 L810,480 L0,480 Z" fill="var(--white)"/>
      <path transform="translate(0,-2)" d="M0,225 C110,330 250,370 450,312 S700,215 810,250 L810,480 L0,480 Z" fill="var(--ember)"/>
    </g>
    <ellipse cx="215" cy="95" rx="290" ry="232" fill="var(--sun)"/>
    <ellipse cx="215" cy="95" rx="288" ry="230" fill="var(--coral)"/>
    <ellipse cx="215" cy="95" rx="280" ry="223" fill="var(--white)"/>
    <ellipse cx="215" cy="95" rx="276" ry="219" fill="none" stroke="var(--ember)" stroke-width="1.2"/>
  </svg>

  <div class="line brand-front">BrindleStaffing</div>
  <div class="line holder-name">Gordon Pratley</div>
  <div class="line holder-title">Chairman</div>

  <div class="line address address-street">417 39th avenue south</div>
  <div class="line address address-city">Saint petersburg fl 33712</div>

  <div class="line contact contact-phone">813-555-4172
    <svg viewBox="0 0 20 20" aria-hidden="true"><circle cx="10" cy="10" r="8.5" fill="none" stroke="#fff" stroke-width="1.5"/><path d="M7.5 5.5c-1.5 1-1.2 4 .6 6.3s4.2 3.3 5.3 2.3l-1.6-2.2-1.3.6c-.8-.5-1.8-1.9-2-2.8l1.1-.9z" fill="#fff"/></svg>
  </div>
  <div class="line contact contact-fax">813-555-8036
    <svg viewBox="0 0 20 20" aria-hidden="true"><rect x="6" y="2.5" width="8" height="5" fill="none" stroke="#fff" stroke-width="1.4"/><rect x="2.5" y="7.5" width="15" height="7" rx="1.5" fill="#fff"/><rect x="6" y="12" width="8" height="5.5" fill="#fff" stroke="#f37122" stroke-width="1"/></svg>
  </div>
  <div class="line contact contact-email">gpratley@brindlestaffing.com
    <svg viewBox="0 0 20 20" aria-hidden="true"><path d="M2 8l8-5 8 5v9H2z" fill="#fff"/><path d="M2 8l8 5 8-5" fill="none" stroke="#f37122" stroke-width="1.5"/></svg>
  </div>
  <div class="line contact contact-web">www.brindlestaffing.com
    <svg viewBox="0 0 20 20" aria-hidden="true"><g fill="none" stroke="#fff" stroke-width="1.3"><circle cx="10" cy="10" r="8"/><ellipse cx="10" cy="10" rx="3.5" ry="8"/><path d="M2 10h16M3.5 6h13M3.5 14h13"/></g></svg>
  </div>
</section>

<section class="card card-back" aria-label="Business card back">
  <div class="line brand-back">BrindleStaffing</div>
  <div class="line web-back">www.<b>brindlestaffing</b>.com</div>
</section>

</body>
</html>
```